ORV Web Design Project

I'm looking for a small, friendly,functional, information based website. If you go through the attachments, you would know the nature of the business.
Updates

Hi,

I have uploaded a picture of the CEO, Mr. Delvan Kroth PLMAT member. Please feel free to use it whereever appropriate.

Thanks!

Hello, I have uploaded some references. I like the colours used on the bar and would w

Example of a we page . I like this layout for the inside pages.

I am changing the tabs on my website to:

Home
About us
Services
Contact us

The services tab will have three sub pages:

Immigration
Education
AccommodationAccommodation

Target Market(s)

Young international students willing to come to Canada to study, young international students willing to immigrate to Canada, parents of the students

Industry/Entity Type

Business

Requirements
Must have
• ORV HOME
ABOUT US
CONTACT
SERVICES
TAG LINE

The website should look n feel trendy, smart, current, factual, trustworthy etc....
Nice to have
• I am looking for a bold, attractive, eye catchy home page with less text! Something that makes a statement....
Should not have
• No Clip art, flash animation, no bells n whistles please

```html
<!DOCTYPE html>
<html lang="en">
<head>
<meta charset="utf-8">
<title>ORV – Orvik Ridge Ventures</title>
<link href="https://fonts.googleapis.com/css2?family=Montserrat:wght@600;700&family=Open+Sans:ital,wght@0,400;0,600;0,700;1,400;1,600&family=Oswald:wght@400&family=Questrial&family=Dosis:wght@500&family=Courgette&display=swap" rel="stylesheet">
<style>
:root{
  --red:#c8161d;
  --red-dark:#9b0a0f;
  --band:#a30006;
  --ink:#1c1c1c;
  --text:#333;
  --nav:#2e2e2e;
  --panel:#e7e7e7;
  --sheet:#f4f4f4;
  --footer:#050505;
  --footer-link:#b5b5b5;
  --green:#3a9a2a;
  --sky:#6f9fe0;
}
*{box-sizing:border-box;margin:0;padding:0}
html,body{width:1033px;height:1200px;overflow:hidden}
body{position:relative;background:linear-gradient(90deg,#c9c9c9 0,#ececec 11%,#ececec 89%,#c9c9c9 100%);font-family:"Open Sans",Arial,sans-serif;color:var(--text)}
.abs{position:absolute}

/* header */
.site-header{left:0;top:0;width:1033px;height:103px;background:linear-gradient(#fafafa,#dcdcdc)}
.brand{left:137px;top:38px;display:flex;align-items:center;gap:9px}
.brand-mark{width:32px;height:32px;background:var(--red)}
.brand-name{font-weight:700;font-size:19px;line-height:21px;color:#6b6b6b}
.tagline{left:200px;top:90px;font-size:7px;font-style:italic;color:#555}
.social{left:748px;top:12px;display:flex;gap:9px}
.social span{width:24px;height:24px;border-radius:4px;background:linear-gradient(#9aa0a6,#6e747a)}
.contact-line{right:129px;font-family:"Questrial",sans-serif;color:#444;white-space:nowrap}
.contact-line b{font-family:"Open Sans",sans-serif;font-weight:400;color:var(--red)}
.call{top:55px;font-size:17px}
.call b{font-size:14px}
.mail{top:79px;font-size:16px}
.mail b{font-size:14px}

/* navigation */
.main-nav{left:0;top:103px;width:1033px;height:27px;background:var(--nav)}
.main-nav a{position:absolute;top:0;color:#fff;text-decoration:none;font-family:"Montserrat",sans-serif;font-weight:600;font-size:10.5px;letter-spacing:.2px;line-height:28px}

/* hero */
.hero-band{left:0;top:130px;width:1033px;height:308px;background:var(--band)}
.hero{left:117px;top:131px;width:799px;height:307px;overflow:hidden}
.hero-photo{position:absolute;inset:0;background:
  radial-gradient(ellipse 130px 110px at 85% 78%,rgba(255,255,255,.95),rgba(255,255,255,0) 100%),
  radial-gradient(ellipse 230px 160px at 88% 85%,#d64a4f 0,rgba(214,74,79,0) 100%),
  radial-gradient(ellipse 260px 70px at 25% 100%,#6f6860 0,rgba(111,104,96,0) 100%),
  radial-gradient(ellipse 170px 150px at 15% 55%,#c89a4a 0,rgba(200,154,74,0) 100%),
  radial-gradient(ellipse 170px 150px at 40% 55%,#b04a4e 0,rgba(176,74,78,0) 100%),
  radial-gradient(ellipse 160px 150px at 60% 60%,#c9c24e 0,rgba(201,194,78,0) 100%),
  radial-gradient(ellipse 120px 120px at 68% 40%,#7b7f96 0,rgba(123,127,150,0) 100%),
  linear-gradient(180deg,#4d82d6 0,#8db3e6 45%,#c6d3e4 100%)}
.hero-title{position:absolute;font-family:"Courgette",cursive;color:#fff;text-shadow:2px 2px 3px rgba(0,0,0,.6);font-size:34px;letter-spacing:1px}
.hero-title.red{color:#e01a20}
.slide-arrow{position:absolute;top:131px;width:24px;height:24px}

/* services */
.services{left:128px;top:446px;width:787px;height:99px;background:linear-gradient(#f6f6f6,#e6e6e6);border:1px solid #d3d3d3}
.services-ribbon{left:117px;top:463px;width:150px;height:70px}
.services-ribbon span{position:absolute;left:12px;top:17px;font-family:"Oswald",sans-serif;font-style:italic;font-size:20px;color:#fff;letter-spacing:.3px}
.service-card{top:452px;width:207px;height:85px;border:1px solid var(--red);border-radius:3px;background:linear-gradient(#fff,#ececec)}
.service-card .thumb{position:absolute;left:5px;top:6px;width:105px;height:72px}
.service-card h3{position:absolute;left:115px;top:3px;font-family:"Oswald",sans-serif;font-weight:400;font-size:12.5px;line-height:19px;color:#222;letter-spacing:.3px}
.more{font-size:9px;color:var(--red);display:inline-flex;align-items:center;gap:2px;text-decoration:none}
.more i{display:inline-block;width:0;height:0;border:4px solid transparent;border-left:6px solid var(--green);border-right:0}
.more.red i{border-left-color:var(--red)}
.service-card .more{position:absolute;left:115px;top:68px}

/* welcome */
.content{left:117px;top:545px;width:799px;height:423px;background:var(--sheet)}
.welcome-title{left:132px;top:564px;font-family:"Montserrat",sans-serif;font-weight:700;font-size:18px;color:var(--ink);letter-spacing:.4px}
.ceo-photo{left:133px;top:600px;width:245px;height:163px;background:
  radial-gradient(ellipse 70px 85px at 50% 45%,#8a8a8a 0,rgba(138,138,138,0) 100%),
  radial-gradient(ellipse 110px 60px at 50% 100%,#1e1e1e 0,rgba(30,30,30,0) 100%),
  radial-gradient(ellipse 180px 140px at 50% 40%,#d2d2d2,#5a5a5a 100%)}
.ceo-bio{left:388px;top:598px;width:256px;font-size:9.6px;line-height:14px;text-align:justify;color:#222}
.ceo-more{left:386px;top:752px}
.mission{left:660px;top:563px;width:243px;height:200px;border:1px solid var(--red);background:linear-gradient(#c21c22,#8d0a0e);padding:42px 18px 0}
.mission h2{position:absolute;left:44px;top:12px;font-family:"Montserrat",sans-serif;font-size:14px;color:#fff;letter-spacing:.5px}
.mission .dot{position:absolute;left:23px;top:10px;width:16px;height:16px}
.mission p{font-style:italic;font-weight:600;font-size:11.4px;line-height:12.5px;color:#fff;text-shadow:1px 1px 1px rgba(0,0,0,.4)}

/* lower panels */
.lower{left:132px;top:787px;width:771px;height:166px;background:var(--panel)}
.panel-title{font-family:"Questrial",sans-serif;font-weight:400;font-size:16px;color:#777;letter-spacing:.6px;display:flex;align-items:center;gap:4px;top:796px}
.panel-title em{font-style:normal;color:var(--red)}
.divider{top:815px;width:1px;height:130px;background:#c9c9c9}
.gallery-thumb{width:97px;height:59px}
.news-date{left:398px;width:52px;height:52px}
.news-item{left:461px;width:140px}
.news-item h4{font-weight:700;font-size:10px;color:var(--red);line-height:13px}
.news-item p{font-size:10px;line-height:12px;color:#222}
.news-item .more{float:right;margin-top:3px}
.news-rule{left:402px;top:881px;width:196px;border-top:1px dashed var(--red)}
.student-photo{left:645px;top:821px;width:79px;height:82px;border:2px solid #fff;background:
  radial-gradient(ellipse 22px 28px at 50% 45%,#b68566 0,rgba(182,133,102,0) 100%),
  radial-gradient(ellipse 40px 20px at 50% 100%,#3fb3d6 0,rgba(63,179,214,0) 100%),
  linear-gradient(#e8eef0,#b9c8cf)}
.student-name{left:637px;top:905px;width:95px;text-align:center;font-size:10px;line-height:15px;color:#222}
.student-name span{display:block;color:var(--red)}
.quote-mark{left:728px;top:814px;font-size:30px;color:#ccc;font-family:Georgia,serif}
.quote{left:740px;top:820px;width:148px;font-size:9.7px;line-height:13.3px;color:#222}
.quote-more{left:835px;top:925px}

/* footer */
.site-footer{left:0;top:968px;width:1033px;height:204px;background:var(--footer)}
.footer-title{top:987px;font-family:"Dosis",sans-serif;font-weight:500;font-size:15px;color:#fff}
.footer-title::after{content:"";display:block;width:90px;height:1px;margin-top:6px;background:linear-gradient(90deg,#555,transparent)}
.sitemap{left:133px;top:1020px;list-style:none}
.sitemap li{font-size:12.5px;line-height:19.6px;color:var(--footer-link)}
.field{left:408px;width:174px;border:1px solid #666;border-radius:4px;background:linear-gradient(#2b2b2b,#1a1a1a);font-size:9px;color:#888;padding:4px 9px}
.send{left:456px;top:1136px;width:72px;height:19px;border-radius:3px;background:var(--red);color:#fff;font-size:11px;text-align:center;line-height:19px}
.footer-art{left:762px;top:993px;width:141px;height:77px;border:1px solid #ddd;background:
  radial-gradient(ellipse 40px 30px at 50% 50%,#fff 0,rgba(255,255,255,0) 100%),
  radial-gradient(ellipse 80px 45px at 50% 50%,#d9363c 0,#f1b9bb 70%,#fff 100%)}
.member-badge{left:757px;top:1090px;width:66px;height:66px}
.legal{left:0;top:1172px;width:1033px;height:28px;background:#1b1b1b;border-top:1px solid #333;text-align:center;font-size:8px;line-height:28px;color:#888}
</style>
</head>
<body>

<header class="site-header abs"></header>
<div class="brand abs">
  <span class="brand-mark"></span>
  <span class="brand-name">ORV<br>Orvik Ridge Ventures</span>
</div>
<div class="tagline abs">Taking you onwards......</div>
<div class="social abs" aria-label="Social links">
  <span></span><span></span><span></span><span></span><span></span>
</div>
<div class="contact-line call abs"><b>Call now:</b> (705) 555 0142</div>
<div class="contact-line mail abs"><b>Email:</b>info@orvikridgeventures.com</div>

<nav class="main-nav abs">
  <a href="#" style="left:132px">HOME</a>
  <a href="#" style="left:195px">ABOUT US</a>
  <a href="#" style="left:283px">SERVICES</a>
  <a href="#" style="left:367px">TESTIMONIALS</a>
  <a href="#" style="left:479px">GALLERY</a>
  <a href="#" style="left:560px">CONTACT US</a>
</nav>

<div class="hero-band abs"></div>
<section class="hero abs">
  <div class="hero-photo" role="img" aria-label="Group of students reading books on a stone wall in front of a city campus, with a red maple-leaf word cloud at lower right"></div>
  <div class="hero-title" style="left:366px;top:4px">Dare to</div>
  <div class="hero-title red" style="left:478px;top:48px">Dream</div>
  <div class="hero-title" style="left:568px;top:90px">Canadian</div>
  <svg class="slide-arrow" style="left:4px" viewBox="0 0 24 24"><circle cx="12" cy="12" r="11" fill="rgba(255,255,255,.45)" stroke="#fff"/><path d="M14 7l-5 5 5 5" fill="none" stroke="#555" stroke-width="2"/></svg>
  <svg class="slide-arrow" style="left:763px" viewBox="0 0 24 24"><circle cx="12" cy="12" r="11" fill="rgba(255,255,255,.45)" stroke="#fff"/><path d="M10 7l5 5-5 5" fill="none" stroke="#555" stroke-width="2"/></svg>
</section>

<section class="services abs"></section>
<div class="services-ribbon abs">
  <svg width="150" height="70" viewBox="0 0 150 70"><path d="M0 8h128l20 24-20 24H0z" fill="#d11a21"/><path d="M0 56h10v12z" fill="#6e0508"/></svg>
  <span>OUR SERVICES</span>
</div>
<div class="service-card abs" style="left:268px">
  <div class="thumb" role="img" aria-label="Immigration application form with a pen" style="background:radial-gradient(ellipse 50px 25px at 55% 75%,#e27d80 0,rgba(226,125,128,0) 100%),linear-gradient(135deg,#f4f4f4,#d6d6d6)"></div>
  <h3>IMMIGRATION<br>SERVICES</h3>
  <a class="more" href="#">Learn more <i></i></a>
</div>
<div class="service-card abs" style="left:483px">
  <div class="thumb" role="img" aria-label="Students working together in a classroom" style="background:radial-gradient(ellipse 40px 25px at 45% 80%,#8e4fa8 0,rgba(142,79,168,0) 100%),linear-gradient(180deg,#d8c7a0,#8a7a68)"></div>
  <h3>EDUCATION<br>SERVICES</h3>
  <a class="more" href="#">Learn more <i></i></a>
</div>
<div class="service-card abs" style="left:697px">
  <div class="thumb" role="img" aria-label="Student residence room with bunk beds and a desk" style="background:radial-gradient(ellipse 30px 40px at 20% 40%,#5b7fa8 0,rgba(91,127,168,0) 100%),linear-gradient(180deg,#c9b89a,#7c6750)"></div>
  <h3>STUDENT<br>ACCOMODATION<br>SERVICES</h3>
  <a class="more" href="#">Learn more <i></i></a>
</div>

<div class="content abs"></div>
<h1 class="welcome-title abs">WELCOME TO ORVIKRIDGEVENTURES - ORV</h1>
<div class="ceo-photo abs" role="img" aria-label="Black and white portrait of the CEO, Delvan Kroth"></div>
<p class="ceo-bio abs">Delvan Kroth, CEO of Orvik Ridge Ventures, has vast knowledge in the field of Student Recruitment &amp; Higher Education. He is an MBA from Canada and is very well known in the India-Canada education corridor since 2004. He has served as India, Africa &amp; Middle East Head for Northgate College in the past, in addition to providing consultant services for various elite institutions including, Harwell College, BC, Pinecrest College, Ottawa, Lakeview Technical College, Manitoba, and Westbay College, BC.</p>
<a class="more red ceo-more abs" href="#">Learn more <i></i></a>

<aside class="mission abs">
  <svg class="dot" viewBox="0 0 16 16"><circle cx="8" cy="8" r="6" fill="none" stroke="#fff" stroke-width="2"/></svg>
  <h2>ORV MISSION</h2>
  <p>At ORV we are committed to our customer centered philosophy. Our mission is to help our clients achieve their goals by providing them with world class customer service that is both reliable and competitively superior. We are driven by our core values: ethics, expertise and leadership. We believe that honesty paves the way for true success. We have been there. We know what it takes.</p>
</aside>

<section class="lower abs"></section>

<h2 class="panel-title abs" style="left:142px">
  <svg width="20" height="16" viewBox="0 0 20 16"><rect x="1" y="2" width="18" height="12" fill="none" stroke="#444" stroke-width="2"/><rect x="4" y="5" width="12" height="6" fill="#444"/></svg>
  <span>GAL<em>LERY</em></span>
</h2>
<div class="gallery-thumb abs" style="left:142px;top:821px;background:radial-gradient(ellipse 40px 25px at 50% 60%,#e0b93a 0,rgba(224,185,58,0) 100%),linear-gradient(#9fc4e8,#c9b48a)" role="img" aria-label="Students celebrating together"></div>
<div class="gallery-thumb abs" style="left:244px;top:821px;background:linear-gradient(#1b3f8c,#3f7cc4 55%,#d48a3a 80%,#2a3d66)" role="img" aria-label="City skyline at dusk"></div>
<div class="gallery-thumb abs" style="left:142px;top:884px;background:linear-gradient(#9cc0e6,#7e8a84 45%,#5d7040 80%,#4f6d36)" role="img" aria-label="Historic university building"></div>
<div class="gallery-thumb abs" style="left:244px;top:884px;background:radial-gradient(ellipse 45px 28px at 50% 55%,#c9906e 0,rgba(201,144,110,0) 100%),linear-gradient(135deg,#e4dcd2,#8a9a6a)" role="img" aria-label="Group of smiling students"></div>

<div class="divider abs" style="left:366px"></div>

<h2 class="panel-title abs" style="left:390px">
  <svg width="26" height="18" viewBox="0 0 26 18"><rect x="1" y="1" width="24" height="16" rx="2" fill="none" stroke="#444" stroke-width="2"/><rect x="4" y="4" width="7" height="6" fill="#444"/><path d="M13 5h9M13 9h9M4 13h18" stroke="#444" stroke-width="1.6"/></svg>
  <span>LATEST <em>NEWS</em></span>
</h2>
<svg class="news-date abs" style="top:818px" viewBox="0 0 52 52"><circle cx="26" cy="26" r="24" fill="#fff" stroke="#555" stroke-width="2"/><circle cx="26" cy="26" r="19" fill="none" stroke="#555" stroke-width="1"/><text x="26" y="28" text-anchor="middle" font-family="Oswald,sans-serif" font-size="16" fill="#c8161d">29</text><text x="26" y="39" text-anchor="middle" font-family="Oswald,sans-serif" font-size="6.5" fill="#c8161d">AUGUST</text></svg>
<div class="news-item abs" style="top:825px">
  <h4>Lorem Ipsum proin gravid</h4>
  <p>Lorem Ipsum. Proin gravida nibh is vel veli auctor aliq..</p>
  <a class="more red" href="#">Learn more <i></i></a>
</div>
<div class="news-rule abs"></div>
<svg class="news-date abs" style="top:887px" viewBox="0 0 52 52"><circle cx="26" cy="26" r="24" fill="#fff" stroke="#555" stroke-width="2"/><circle cx="26" cy="26" r="19" fill="none" stroke="#555" stroke-width="1"/><text x="26" y="28" text-anchor="middle" font-family="Oswald,sans-serif" font-size="16" fill="#c8161d">30</text><text x="26" y="39" text-anchor="middle" font-family="Oswald,sans-serif" font-size="6.5" fill="#c8161d">AUGUST</text></svg>
<div class="news-item abs" style="top:894px">
  <h4>Lorem Ipsum proin gravid</h4>
  <p>Lorem Ipsum. Proin gravid nibh is vel veli auctor aliq..</p>
  <a class="more red" href="#">Learn more <i></i></a>
</div>

<div class="divider abs" style="left:625px"></div>

<h2 class="panel-title abs" style="left:650px">
  <svg width="28" height="18" viewBox="0 0 28 18"><ellipse cx="10" cy="7" rx="9" ry="6" fill="#444"/><ellipse cx="19" cy="10" rx="8" ry="5.5" fill="#666"/><path d="M5 11l-2 5 6-3z" fill="#444"/></svg>
  <span>WHAT <em>STUDENT SAY!!</em></span>
</h2>
<div class="student-photo abs" role="img" aria-label="Portrait of student Anika Devran"></div>
<div class="student-name abs">Anika Devran<span>India</span></div>
<div class="quote-mark abs">&ldquo;</div>
<p class="quote abs">Lorem Ipsum. Proin gravidap nibh is vel veli auctor aliquet Aenean soik licitudin, loremik quis bibendum auct nisi elit a consetop qua ipsum, nec kih sagittis sem nibh id elit jmdti odio sit amet nibh vulputates ai cursus a sit amet maurisng</p>
<a class="more red quote-more abs" href="#">Learn more <i></i></a>

<footer class="site-footer abs"></footer>
<h3 class="footer-title abs" style="left:132px">Site map</h3>
<ul class="sitemap abs">
  <li>- Home</li><li>- About Us</li><li>- Services</li><li>- Testimonials</li><li>- Gallery</li><li>- Contact Us</li>
</ul>
<h3 class="footer-title abs" style="left:410px">Quick Contact</h3>
<div class="field abs" style="top:1024px;height:21px">Name..</div>
<div class="field abs" style="top:1050px;height:21px">Email..</div>
<div class="field abs" style="top:1076px;height:54px">Message..</div>
<div class="send abs">Send</div>
<div class="footer-art abs" role="img" aria-label="Red and white maple-leaf word cloud"></div>
<svg class="member-badge abs" viewBox="0 0 66 66" role="img" aria-label="Professional membership badge"><circle cx="33" cy="33" r="32" fill="#1f5fa3"/></svg>
<div class="legal abs">Copyright 2013 Orvik Ridge Ventures. All rights reserved.</div>

</body>
</html>
```